Design Direct mailer post card for Carpet Cleaning business

We are looking to create a 6.5x 12 eyes cashing direct mail postcard (eddm) for mailed to residential .
This campaign is targeted towards residential customers, with the goal of introducing our service, promote our business, and gain some brand recognition.
The call-to-action is for the prospect to contact us and also schedule a free no obligation demonstration (call, visit our website, or send us an email) to find out information about our service, and to learn more about our service.
4 offers
One Free Room of carpet cleaning
Free bottle spot cleaner
Free Carpet audit
Free chair Cleaning
(See attached picture for offers)
Slogans-You will love your Carpet Again
You want believe the difference
No more Wet Carpet
Dries in minutes not hours
100% natural Safe for Kids and Pets
No harsh chemicals
No sticky residue
Improve air Quailty
100% guaranteed
As far as design, we are looking for a clean and simple layout, not too cluttered, but powerful enough to grab the attention of the reader. Less is more in this case. On the front we were thinking the use of an image & headline and on the back the rest of the information. With that said, please feel free to use your expertise and judgement to conceptualize the best design.
Also attach picture of design and color that I would like.
Target Market(s)
35-70 women middle to upper class
Industry/Entity Type
Cleaning Service

```html
<!DOCTYPE html>
<html lang="en">
<head>
<meta charset="utf-8">
<title>VerdaClean Direct Mail Postcard</title>
<link href="https://fonts.googleapis.com/css2?family=Roboto:wght@300;400;500&family=Roboto+Condensed:wght@400;500;700&family=Dancing+Script:wght@500&display=swap" rel="stylesheet">
<style>
  :root{
    --teal:#1fbcd2;
    --teal-light:#c4ecf3;
    --green:#8dc63f;
    --green-dark:#6fae2a;
    --orange:#f07b22;
    --ink:#2a2a2a;
    --paper:#ffffff;
    --backdrop:#e6e6e6;
  }
  *{box-sizing:border-box;margin:0;padding:0}
  html,body{width:1102px;height:1200px;overflow:hidden}
  body{background:var(--backdrop);font-family:"Roboto",sans-serif;color:var(--ink);position:relative}
  .card{position:absolute;left:16px;width:1070px;height:575px;background:var(--paper);overflow:hidden;box-shadow:0 2px 6px rgba(0,0,0,.25)}
  .card--front{top:14px}
  .card--back{top:611px}
  .card__art{position:absolute;inset:0;width:1070px;height:575px}
  .abs{position:absolute}

  .brand{position:absolute;display:flex;align-items:center;gap:12px}
  .brand__dot{width:26px;height:26px;border-radius:50%;background:var(--teal)}
  .brand__name{font-family:"Roboto",sans-serif;font-weight:300;font-size:64px;line-height:1;color:var(--green)}
  .brand__tag{font-family:"Roboto",sans-serif;font-weight:300;font-size:21px;color:var(--teal);margin-top:2px}
  .brand--light .brand__dot{background:#fff}
  .brand--light .brand__name,.brand--light .brand__tag{color:#fff}

  .headline{font-family:"Roboto Condensed",sans-serif;font-weight:500;color:#fff;font-size:29px;letter-spacing:.3px}

  .checklist{list-style:none}
  .checklist li{display:flex;align-items:center;gap:8px;font-size:19px;line-height:27.6px}
  .tick{width:15px;height:15px;flex:none}

  .dry-badge{left:448px;top:375px;width:180px;height:180px;border-radius:50%;background:var(--orange);border:6px solid #f2f2f2;box-shadow:0 2px 5px rgba(0,0,0,.25);color:#fff;text-align:center;padding-top:33px}
  .dry-badge__title{font-weight:500;font-size:15px;line-height:18px}
  .dry-badge__text{font-size:14.5px;line-height:18px;margin-top:6px}

  .experts{left:30px;top:470px;color:#fff}
  .experts__title{font-family:"Roboto Condensed",sans-serif;font-weight:500;font-size:22px;margin-bottom:10px}
  .experts__text{font-size:16.5px;line-height:23px;width:420px}

  .contact{color:#fff;text-align:center}
  .contact__phone{display:flex;align-items:center;gap:10px;font-weight:400;font-size:45px;line-height:1}
  .contact__phone svg{width:38px;height:38px}
  .contact__web{font-size:17px;margin-top:8px}

  .services{left:28px;top:22px;display:grid;grid-template-columns:205px 243px 220px;row-gap:6px}
  .services li{list-style:none;display:flex;align-items:center;gap:8px;font-size:21.5px;color:#333}

  .mail-box{left:718px;top:30px;width:240px;height:84px;border:1px solid #444;font-size:13px;padding:10px 16px}
  .mail-box__code{text-align:right;font-size:11px;letter-spacing:.5px}
  .mail-box__to{margin-top:18px;line-height:14px}
  .indicia{left:979px;top:30px;width:84px;height:84px;border:1px solid #444;font-weight:500;font-size:11px;line-height:13px;text-align:center;padding-top:9px}

  .coupons{left:30px;top:170px;display:flex;gap:20px}
  .coupon{width:245px;height:130px;background:#fff;box-shadow:0 1px 4px rgba(0,0,0,.3);padding:6px 4px 4px}
  .coupon__head{display:flex;justify-content:space-between;align-items:flex-start;padding:0 6px;height:53px;position:relative}
  .coupon__free{font-family:"Roboto Condensed",sans-serif;font-weight:700;font-size:28px;color:var(--green);line-height:1}
  .coupon__offer{font-family:"Roboto Condensed",sans-serif;font-size:21px;color:var(--green);line-height:20px;text-align:right;margin-top:6px}
  .coupon__script{position:absolute;left:8px;top:32px;font-family:"Dancing Script",cursive;font-size:13px;color:var(--green-dark)}
  .coupon__body{background:var(--green);height:67px;border:2px dashed rgba(255,255,255,.85);outline:3px solid var(--green);color:#fff;font-size:8.7px;line-height:11.5px;padding:4px 6px;margin:3px}

  .specials{left:30px;top:318px;width:820px;font-size:21px;line-height:31px;color:#222}
</style>
</head>
<body>
<svg width="0" height="0" style="position:absolute">
  <defs>
    <symbol id="tick" viewBox="0 0 16 16">
      <rect x="1" y="3" width="11" height="11" rx="1.5" fill="none" stroke="#8dc63f" stroke-width="1.6"/>
      <path d="M4 8 L7 11 L15 2" fill="none" stroke="#8dc63f" stroke-width="2" stroke-linecap="round" stroke-linejoin="round"/>
    </symbol>
    <symbol id="phone" viewBox="0 0 40 40">
      <circle cx="20" cy="20" r="18" fill="none" stroke="#fff" stroke-width="2.5"/>
      <path d="M13 11 c2-2 4-1 5 1 l1.5 3 c.6 1.3 0 2.3-1 3 c1 2.5 3 4.5 5.5 5.5 c.7-1 1.7-1.6 3-1 l3 1.5 c2 1 3 3 1 5 c-2 2-5 3-9 0 c-4-3-7-6-9-10 c-2-4-1.5-6 0-8z" fill="#fff"/>
    </symbol>
  </defs>
</svg>

<!-- FRONT -->
<section class="card card--front">
  <svg class="card__art" viewBox="0 0 1070 575">
    <defs>
      <linearGradient id="photoTone" x1="0" y1="0" x2="1" y2="1">
        <stop offset="0" stop-color="#e9e6e2"/>
        <stop offset=".5" stop-color="#d9c8b9"/>
        <stop offset="1" stop-color="#efece6"/>
      </linearGradient>
    </defs>
    <path d="M608 0 H1070 V440 C900 430 760 440 640 470 C560 380 545 200 608 0 Z" fill="url(#photoTone)" role="img" aria-label="Photo of a smiling child and a small dog lying on a soft white carpet"/>
    <path d="M598 0 C536 200 550 380 630 470" fill="none" stroke="var(--teal)" stroke-width="14"/>
    <path d="M600 458 C790 488 950 420 1070 372 V420 C950 455 800 488 640 472 Z" fill="var(--green)"/>
    <polygon points="0,128 602,128 580,196 0,196" fill="var(--green)"/>
    <path d="M0 455 C250 405 450 420 640 462 C800 492 950 432 1070 418" fill="none" stroke="var(--teal-light)" stroke-width="12"/>
    <path d="M0 468 C250 418 450 432 640 474 C800 504 950 444 1070 430 V575 H0 Z" fill="var(--teal)"/>
    <path d="M968 0 H1060 V82 L1014 98 L968 82 Z" fill="var(--orange)" role="img" aria-label="Award badge"/>
    <circle cx="413" cy="354" r="40" fill="var(--green)" role="img" aria-label="Eco friendly badge"/>
  </svg>

  <div class="brand" style="left:62px;top:30px">
    <span class="brand__dot"></span>
    <div>
      <div class="brand__name">VerdaClean</div>
      <div class="brand__tag">Carpet Cleaning &amp; Restoration</div>
    </div>
  </div>

  <h1 class="headline abs" style="left:28px;top:143px">YOU WILL LOVE YOUR CARPET AGAIN</h1>

  <ul class="checklist abs" style="left:28px;top:210px">
    <li><svg class="tick"><use href="#tick"/></svg>No more Wet Carpet</li>
    <li><svg class="tick"><use href="#tick"/></svg>Dries in minutes not hours</li>
    <li><svg class="tick"><use href="#tick"/></svg>100% natural Safe for Kids and Pets</li>
    <li><svg class="tick"><use href="#tick"/></svg>No harsh chemicals</li>
    <li><svg class="tick"><use href="#tick"/></svg>No sticky residue</li>
    <li><svg class="tick"><use href="#tick"/></svg>Improve air Quailty</li>
    <li><svg class="tick"><use href="#tick"/></svg>100% guaranteed</li>
  </ul>

  <div class="dry-badge abs">
    <div class="dry-badge__title">FAST ONE HOUR<br>DRY TIME</div>
    <div class="dry-badge__text">Soft Drying With No<br>Crunchy Residue<br>Safe for Children<br>&amp; Pets</div>
  </div>

  <div class="experts abs">
    <h2 class="experts__title">Pet Odor &amp; Stain Removal Experts</h2>
    <p class="experts__text">Contact us and also schedule a free no obligation demonstration (call, visit our website, or send us an email) to find out information about our service.</p>
  </div>

  <div class="contact abs" style="left:690px;top:492px">
    <div class="contact__phone"><svg><use href="#phone"/></svg>555.014.2270</div>
    <div class="contact__web">www.verdacleancarpets.com</div>
  </div>
</section>

<!-- BACK -->
<section class="card card--back">
  <svg class="card__art" viewBox="0 0 1070 575">
    <defs>
      <linearGradient id="roomTone" x1="0" y1="0" x2="1" y2="0">
        <stop offset="0" stop-color="#f0f0f0"/>
        <stop offset="1" stop-color="#e2e2e2"/>
      </linearGradient>
    </defs>
    <rect x="0" y="142" width="1070" height="340" fill="url(#roomTone)" role="img" aria-label="Faint photo of a bright living room"/>
    <path d="M0 95 H676 V85 L692 97 V144 H0 Z" fill="var(--teal)"/>
    <path d="M600 440 C800 440 960 420 1070 365 V405 C960 455 800 462 640 452 Z" fill="var(--green)"/>
    <path d="M0 445 C300 392 550 425 750 448 C900 462 1000 412 1070 392" fill="none" stroke="var(--teal-light)" stroke-width="12"/>
    <path d="M0 458 C300 405 550 438 750 461 C900 475 1000 425 1070 405 V575 H0 Z" fill="var(--teal)"/>
    <circle cx="808" cy="408" r="65" fill="#d9d3cb" stroke="#f2f2f2" stroke-width="6" role="img" aria-label="Photo of clean floor tiles"/>
    <circle cx="955" cy="382" r="85" fill="#8c8a6a" stroke="#f2f2f2" stroke-width="6" role="img" aria-label="Photo of an armchair being cleaned with an upholstery tool"/>
  </svg>

  <ul class="services abs">
    <li><svg class="tick"><use href="#tick"/></svg>Carpet Cleaning</li>
    <li><svg class="tick"><use href="#tick"/></svg>Upholstery Cleaning</li>
    <li><svg class="tick"><use href="#tick"/></svg>Odor Removal</li>
    <li><svg class="tick"><use href="#tick"/></svg>Tile Cleaning</li>
    <li><svg class="tick"><use href="#tick"/></svg>Rug Cleaning</li>
    <li><svg class="tick"><use href="#tick"/></svg>Air Duct Cleaning</li>
  </ul>

  <div class="mail-box abs">
    <div class="mail-box__code">*****************ECRWSS****</div>
    <div class="mail-box__to">Local<br>Postal Customer</div>
  </div>
  <div class="indicia abs">PRSRT STD<br>ECRWSS<br>U.S. POSTAGE<br>PAID<br>EDDM RETAIL</div>

  <h2 class="headline abs" style="left:31px;top:103px">YOU WANT BELIEVE THE DIFFERENCE!</h2>

  <div class="coupons abs">
    <article class="coupon">
      <div class="coupon__head"><span class="coupon__free">FREE</span><span class="coupon__offer">Carpet Audit</span><span class="coupon__script">Save Big!</span></div>
      <p class="coupon__body">No obligation. A carpet audit is more than a quote. We show what we can do to improve your carpet and how long results will last.</p>
    </article>
    <article class="coupon">
      <div class="coupon__head"><span class="coupon__free">FREE</span><span class="coupon__offer">One Room Clean</span><span class="coupon__script">Great Deal!</span></div>
      <p class="coupon__body">Yes, that's right! Try our service before you buy. We clean any one room up to 200 sq. ft. free, no obligation or purchase needed.</p>
    </article>
    <article class="coupon">
      <div class="coupon__head"><span class="coupon__free">FREE</span><span class="coupon__offer">Bottle Of Spot<br>Cleaner</span><span class="coupon__script">Spot Cleaner for Life!</span></div>
      <p class="coupon__body">With any cleaning service we include a free bottle of our professional home spot cleaner, yours for life. (A $89.95 value)</p>
    </article>
    <article class="coupon">
      <div class="coupon__head"><span class="coupon__free">FREE</span><span class="coupon__offer" style="font-size:24px">Chair Cleaning</span><span class="coupon__script">Bonus offer!</span></div>
      <p class="coupon__body">Normally $59.99, but yours free with this offer! Let us clean your sofa or loveseat and we will clean a chair for free.</p>
    </article>
  </div>

  <p class="specials abs">Specials only good for use in willow ridge and cedar glen. If You Wait You'll Miss out! Call 555.014.2270 right now before the coupons expire or run out!</p>

  <div class="brand brand--light" style="left:34px;top:478px">
    <span class="brand__dot"></span>
    <div>
      <div class="brand__name">VerdaClean</div>
      <div class="brand__tag">Carpet Cleaning &amp; Restoration</div>
    </div>
  </div>

  <div class="contact abs" style="left:718px;top:494px">
    <div class="contact__phone"><svg><use href="#phone"/></svg>555.014.2270</div>
    <div class="contact__web">www.verdacleancarpets.com</div>
  </div>
</section>
</body>
</html>
```